I need a logo design for a new company based in Tucson called "Mindtrail Lee Corwin". I am a psychotherapist that specializes in clinical psychology with athletes and performers. The final design should incorporate the psychology symbol as a watermark. The logo should convey movement and fluidity. "Mindtrail" is a bit of a play on words combining psychology (head) with sports (coach). Other design interests include mid-century, Harold Ames Whitby. I will want to use the logo for business cards, letterhead and marketing brochures. I will put together a website at a later date. I am attaching a file with some pertinent information for the business card. Thank you.
Lee Corwin
mindtrailleecorwin@quillpost.net

Thank you all for the submissions so far.  I have submitted an additional file with a draft of a new design idea.  Since "mindtrail" is a bit of a play on words, I would like to see something with the two "H's" look something like quotation marks.  If the psychology logo is to be included at all, it needs to be less prominent.     Thank you all.  Lee                               

Target Market(s)

1) Adolescent and adult athletes and performers who are looking to increase their level of performance (Sport and Performance Psychology)
2) Adult psychotherapy patients (Clinical psychology)

Industry/Entity Type

Marketing

Colors

Designer to choose colors to be used in the design.

Requirements
Must have
• 1) Since "mindtrail" is a bit of a play on words, The "H's" need to be in a font that looks somewhat like quotation marks.

Nice to have
• Logo on one side. All other info on the backside?

```html
<!DOCTYPE html>
<html lang="en">
<head>
<meta charset="utf-8">
<title>Mindtrail Lee Corwin — Business Card</title>
<link href="https://fonts.googleapis.com/css2?family=Alegreya:wght@700&family=Lato:wght@400;700&display=swap" rel="stylesheet">
<style>
  :root {
    --backdrop: #c9cacb;
    --card: #121212;
    --card-glow: #242424;
    --brand-green: #3a9a48;
    --ink-white: #f2f2f2;
  }
  html, body {
    margin: 0;
    padding: 0;
    width: 1200px;
    height: 1000px;
    overflow: hidden;
    background: var(--backdrop);
  }
  .canvas {
    position: relative;
    width: 1200px;
    height: 1000px;
  }
  .card {
    position: absolute;
    width: 640px;
    height: 390px;
    border-radius: 22px;
    background: radial-gradient(ellipse at 50% 45%, var(--card-glow) 0%, var(--card) 70%);
    box-shadow: 0 6px 16px rgba(0,0,0,0.25);
    font-family: 'Lato', sans-serif;
    color: var(--ink-white);
  }
  .card--front { left: 500px; top: 60px; }
  .card--back  { left: 80px;  top: 540px; }

  .brand {
    position: absolute;
    left: 70px;
    top: 95px;
    width: 500px;
  }
  .brand__lockup {
    display: flex;
    align-items: center;
    gap: 22px;
  }
  .brand__mark {
    width: 92px;
    height: 92px;
    background: var(--brand-green);
  }
  .brand__name {
    font-family: 'Lato', sans-serif;
    font-weight: 700;
    font-size: 74px;
    letter-spacing: 2px;
    color: var(--ink-white);
    line-height: 1;
  }
  .brand__tagline {
    margin-top: 26px;
    font-size: 21px;
    letter-spacing: 2.5px;
    text-transform: uppercase;
    white-space: nowrap;
  }

  .person {
    position: absolute;
    top: 90px;
    width: 100%;
    text-align: center;
  }
  .person__name {
    font-family: 'Alegreya', serif;
    font-weight: 700;
    font-size: 30px;
    color: var(--brand-green);
    letter-spacing: 1px;
  }
  .person__title {
    margin-top: 2px;
    font-weight: 700;
    font-size: 17px;
  }
  .contact {
    position: absolute;
    top: 215px;
    width: 100%;
    margin: 0;
    padding: 0;
    list-style: none;
    text-align: center;
    font-size: 18px;
    line-height: 30px;
  }
  .contact__label {
    color: var(--brand-green);
    font-weight: 700;
  }
</style>
</head>
<body>
<main class="canvas">
  <section class="card card--front" aria-label="Card front">
    <div class="brand">
      <div class="brand__lockup">
        <div class="brand__mark"></div>
        <div class="brand__name">Mindtrail</div>
      </div>
      <div class="brand__tagline">Clinical &amp; Performance Psychology</div>
    </div>
  </section>

  <section class="card card--back" aria-label="Card back">
    <div class="person">
      <div class="person__name">Lee H. Corwin,&nbsp; MA</div>
      <div class="person__title">Licensed Professional Counselor</div>
    </div>
    <ul class="contact">
      <li><span class="contact__label">Fax:</span> 520.555.0193</li>
      <li><span class="contact__label">Mobile:</span> 520.555.0147</li>
      <li><span class="contact__label">Email:</span> mindtrailleecorwin@quillpost.net</li>
      <li><span class="contact__label">Address:</span> 4120 East Saguaro #210 Tucson,&nbsp; AZ 85718</li>
    </ul>
  </section>
</main>
</body>
</html>
```